Little Lantern Milestone Day Poster

I need a poster to raise awareness for a condition called Global Developmental Delay (GDD) . The day of awareness for this condition is May 1. The condition is something found in children who are significantly delayed in their milestones. We are hopeful that through education and support more children with this condition can gain access to therapies and support to minimize the long term effects and maxamise their potential. Theme for GDD awareness is yellow so lots of yellow needed. Can be any yellow. Like it to be colourful, but not bright if that makes sense. I'd like it to be classy but fun and childish - this is a childhood diagnosis. Just not 'tacky'. Like the design to reflect the wonders of childhood so feel free to use your imagination!

Target Market(s)

Mums (and dads) of young children under 5

Colors
fee18a
fbf289

Requirements
Must have
• cheery, childish, happy feel - see uploaded poster examples for ideas. They are just ideas for theme. Different fun, childish fonts and 'sections' - perhaps with different colour backgrounds etc.
• Heading should be "Global Developmental Delay" or something similar
• Must have text as in the attachment
• Must have yellow 'theme'
• more colours than just yellow.
Nice to have
• colors - not bright but colorful.

```html
<!DOCTYPE html>
<html lang="en">
<head>
<meta charset="utf-8">
<title>Little Lantern Milestone Day Poster</title>
<link rel="stylesheet" href="https://fonts.googleapis.com/css2?family=Chewy&family=Montserrat:wght@500;600;700&display=swap">
<style>
  :root {
    --stage: #f1efe8;
    --paper: #ffffff;
    --red: #e41f2b;
    --yellow: #fbf289;
    --yellow-soft: #fbf39b;
    --tan: #d3b25a;
    --ink: #1c1c1c;
    --white: #ffffff;
  }
  * { box-sizing: border-box; margin: 0; padding: 0; }
  html, body { width: 1200px; height: 1200px; overflow: hidden; background: var(--stage); }
  body { font-family: "Montserrat", "Trebuchet MS", Arial, sans-serif; color: var(--ink); }
  .poster {
    position: absolute; left: 185px; top: 17px; width: 830px; height: 1166px;
    background: var(--paper); overflow: hidden;
  }
  .poster > * { position: absolute; }
  .display {
    font-family: "Chewy", "Comic Sans MS", "Chalkboard SE", "Comic Neue", cursive;
    font-weight: 400; color: var(--red); line-height: 1;
  }
  .title-top { left: 0; width: 100%; top: 14px; text-align: center; font-size: 100px; }
  .title-bottom { left: 0; width: 100%; top: 112px; text-align: center; font-size: 74px; letter-spacing: 1px; }
  .band { left: 0; top: 200px; width: 830px; height: 480px; }
  .hero-art {
    left: 538px; top: 187px; width: 264px; height: 354px; border-radius: 50% 50% 46% 46%;
    background: linear-gradient(160deg, #f3ddc6 0%, #e9c9a6 35%, #6fb3cf 65%, #ece4d6 100%);
  }
  .what-title { left: 25px; top: 244px; font-size: 56px; }
  .intro { left: 25px; top: 310px; width: 525px; font-size: 14px; font-weight: 500; line-height: 18px; letter-spacing: -0.1px; }
  .checklist { left: 30px; top: 385px; width: 470px; list-style: none; display: grid; grid-template-columns: 228px 220px; row-gap: 12px; }
  .checklist li { display: flex; align-items: center; gap: 4px; font-size: 16px; font-weight: 700; }
  .tick { width: 18px; height: 18px; flex: none; }
  .concern-card {
    left: 44px; top: 480px; width: 315px; height: 279px; border-radius: 8px;
    background: var(--red); box-shadow: 0 6px 8px rgba(0,0,0,.12); overflow: hidden; color: var(--white); text-align: center;
  }
  .concern-art { position: absolute; left: 0; top: 0; width: 100%; height: 86px; background: linear-gradient(#fff 0%, #f7d7b9 45%, #e41f2b 100%); }
  .concern-title { position: absolute; left: 0; width: 100%; top: 96px; font-size: 26px; color: var(--white); }
  .concern-text { position: absolute; left: 12px; right: 12px; top: 127px; font-size: 14px; font-weight: 500; line-height: 18px; }
  .causes-title { left: 411px; top: 522px; font-size: 27px; color: var(--tan); }
  .causes { left: 411px; top: 560px; width: 400px; font-size: 14px; font-weight: 500; line-height: 18px; }
  .causes p + p { margin-top: 14px; }
  .cause-list { list-style: none; margin: 14px 0 14px; }
  .cause-list li { font-size: 16px; font-weight: 700; margin-bottom: 14px; padding-left: 16px; position: relative; }
  .cause-list li::before { content: ""; position: absolute; left: 0; top: 7px; width: 5px; height: 5px; border-radius: 50%; background: var(--red); }
  .do-title { left: 34px; width: 320px; text-align: center; top: 780px; font-size: 27px; color: var(--tan); }
  .do-text { left: 33px; top: 812px; width: 345px; font-size: 14px; font-weight: 500; line-height: 18px; }
  .contact-tab {
    left: 66px; top: 935px; width: 175px; height: 34px; border-radius: 16px 16px 0 0;
    background: var(--yellow); font-size: 23px; font-weight: 600; text-align: center; line-height: 34px;
  }
  .contact-panel { left: 0; top: 966px; width: 310px; height: 162px; background: var(--red); color: var(--white); padding: 12px 0 0 36px; }
  .contact-row { display: flex; align-items: center; gap: 10px; font-size: 12.5px; font-weight: 500; line-height: 15px; margin-bottom: 8px; }
  .contact-row.phone { font-size: 15px; font-weight: 700; margin-bottom: 10px; }
  .contact-row svg { width: 20px; height: 20px; flex: none; }
  .follow { display: flex; align-items: center; gap: 8px; margin: 10px 0 0 40px; font-size: 12.5px; font-weight: 500; }
  .follow .dot { width: 14px; height: 14px; border-radius: 50%; border: 2px solid var(--white); }
  .kids-art {
    left: 320px; top: 945px; width: 470px; height: 180px; border-radius: 40px;
    background: linear-gradient(90deg, #f7b64b 0%, #f58fa0 25%, #3c78c3 50%, #f48a36 70%, #6dc3d9 100%); opacity: .85;
  }
  .footer-band { left: 0; top: 1128px; width: 100%; height: 38px; background: var(--yellow-soft); }
</style>
</head>
<body>
<main class="poster">
  <svg class="band" viewBox="0 0 830 480" aria-hidden="true">
    <path d="M0 10 Q320 -5 610 20 L830 30 L830 330 Q700 300 560 305 L330 300 Q150 310 0 340 Z" fill="var(--yellow)"/>
  </svg>

  <h1 class="display title-top">Global</h1>
  <h1 class="display title-bottom">Developmental Delay</h1>

  <div class="hero-art" role="img" aria-label="Illustration of a sad little boy sitting hugging his knees"></div>

  <h2 class="display what-title">What is GDD ?</h2>
  <p class="intro">A developmental delay is more than being ‘a little behind.” Global developmental delay (GDD)is diagnosed when a child is significantly delayed in two or more of the 5 developmental realms including</p>

  <ul class="checklist">
    <li><svg class="tick" viewBox="0 0 18 18"><rect x="1" y="4" width="12" height="12" fill="none" stroke="var(--red)" stroke-width="1.6"/><path d="M4 9l3 3 9-10" fill="none" stroke="var(--red)" stroke-width="2.2"/></svg>Cognitive (or thinking)</li>
    <li><svg class="tick" viewBox="0 0 18 18"><rect x="1" y="4" width="12" height="12" fill="none" stroke="var(--red)" stroke-width="1.6"/><path d="M4 9l3 3 9-10" fill="none" stroke="var(--red)" stroke-width="2.2"/></svg>Social and emotional</li>
    <li><svg class="tick" viewBox="0 0 18 18"><rect x="1" y="4" width="12" height="12" fill="none" stroke="var(--red)" stroke-width="1.6"/><path d="M4 9l3 3 9-10" fill="none" stroke="var(--red)" stroke-width="2.2"/></svg>Communication</li>
    <li><svg class="tick" viewBox="0 0 18 18"><rect x="1" y="4" width="12" height="12" fill="none" stroke="var(--red)" stroke-width="1.6"/><path d="M4 9l3 3 9-10" fill="none" stroke="var(--red)" stroke-width="2.2"/></svg>Fine motor</li>
    <li><svg class="tick" viewBox="0 0 18 18"><rect x="1" y="4" width="12" height="12" fill="none" stroke="var(--red)" stroke-width="1.6"/><path d="M4 9l3 3 9-10" fill="none" stroke="var(--red)" stroke-width="2.2"/></svg>Gross motor</li>
  </ul>

  <section class="concern-card">
    <div class="concern-art" role="img" aria-label="Illustration of five happy children jumping in a row"></div>
    <h3 class="display concern-title">If you are concerned</h3>
    <p class="concern-text">Early intervention programs and therapies can give many children with global development delays a head start and allow them to reach their full potential. If you are concerned that your child is not developing at the rate you would expect, please talk to your GP.</p>
  </section>

  <h3 class="display causes-title">What causes GDD</h3>
  <div class="causes">
    <p>There are many possible causes of GDD. Some are permanent, but others aren’t.</p>
    <p>They include</p>
    <ul class="cause-list">
      <li>Genetic conditions</li>
      <li>Complications in pregnancy or birth</li>
      <li>Environmental issues</li>
      <li>Other medical conditions</li>
    </ul>
    <p>More often than not a child received a secondary diagnosis as they grow such as intellectual disability or autism spectrum disorder, in which case the name for the disorder replaces the term developmental delay.</p>
  </div>

  <h3 class="display do-title">What can you do?</h3>
  <p class="do-text">Each child is different in their own wonderful way, if we choose to celebrate and understand the things that make us unique as well as the ones that bring us together, we can create a much happier and more inclusive environment for all our children.</p>

  <div class="kids-art" role="img" aria-label="Illustration of four cheerful children jumping with arms raised"></div>

  <div class="contact-tab">Contact us</div>
  <section class="contact-panel">
    <div class="contact-row phone"><svg viewBox="0 0 20 20"><circle cx="10" cy="10" r="8.5" fill="none" stroke="#fff" stroke-width="1.4"/><path d="M7 5.5l2 2-1 1.3c.6 1.3 1.6 2.3 2.9 2.9l1.3-1 2 2-1.2 1.6C9.9 14.2 6 10.3 5.6 7z" fill="#fff"/></svg>01234 567 890</div>
    <div class="contact-row"><svg viewBox="0 0 20 20"><path d="M10 2a5.5 5.5 0 0 0-5.5 5.5C4.5 12 10 18 10 18s5.5-6 5.5-10.5A5.5 5.5 0 0 0 10 2z" fill="#fbd34d"/><circle cx="10" cy="7.5" r="2" fill="var(--red)"/></svg><span>Lorem ipsum dolor sit amet,<br>consectetur adipiscing elit,</span></div>
    <div class="contact-row"><svg viewBox="0 0 20 20"><rect x="2" y="5" width="16" height="11" fill="#fbd34d"/><path d="M2 5l8 6 8-6" fill="none" stroke="var(--red)" stroke-width="1.4"/></svg>hello@littlelantern.org</div>
    <div class="contact-row"><svg viewBox="0 0 20 20"><g fill="none" stroke="#fbd34d" stroke-width="1.4"><circle cx="10" cy="10" r="7.5"/><ellipse cx="10" cy="10" rx="3.5" ry="7.5"/><path d="M2.5 10h15M4 6h12M4 14h12"/></g></svg>www.littlelantern.org</div>
    <div class="follow">Follow us @ <span class="dot"></span> Little Lantern</div>
  </section>

  <div class="footer-band"></div>
</main>
</body>
</html>
```